RKT Advisory Business Cards

Hi there,

I'd like to make a simple new business card design with the logo we already have created for our business.

I need a double sided business card with our logo on the front side and the company and person's details on the back side.

I'd like it to be on a white background and no background so I can potentially use it with either white paper or put it on different coloured paper in accordance with our business colours.

Please use the logo images I have attached and also the fonts.

So Front side:
- Logo in centre of business card (use medium logo so there is a pretty decent border around it, so don't want to fill the whole card but to make it prominent).

Back Side.
- We need 3 different business cards with the different people's name on each.

ie.

Dorian Valecki
Business Development Manager

m +61 455 207 318
e dorian@rktadvisory.example.com.au
w rktadvisory.example.com.au

- Also I'd like to put only the cog/power button logo in the top right hand corner of the card.
(You might need to chop the current logo in half as I don't have a seperate log just for this)
- Also I'd like some lines running on the top left hand corner diagonally, anything that will add to the design or some swirling lines that add some cool effect to the card.

Also I'd like to maybe put our ABN in the bottom right hand corner of the card in a smaller font.

I'd like to also talk to the designer if possible so I can get my idea across a bit better.

Thanks!

Regards,
Dorian

```html
<!DOCTYPE html>
<html lang="en">
<head>
<meta charset="utf-8">
<title>RKT Advisory Business Cards</title>
<link rel="stylesheet" href="https://fonts.googleapis.com/css2?family=Michroma&family=Ubuntu:wght@400;700&display=swap">
<style>
  :root {
    --stage: #ece8e3;
    --card: #ffffff;
    --ink: #4a4a4c;
    --ink-soft: #8a8a8c;
    --orange: #f7941d;
    --orange-pale: #fde6c8;
    --mark: #4f4f51;
  }
  * { margin: 0; padding: 0; box-sizing: border-box; }
  html, body { width: 1200px; height: 1023px; overflow: hidden; }
  body { background: var(--stage); position: relative; font-family: "Ubuntu", sans-serif; }

  .card {
    position: absolute;
    width: 620px;
    height: 378px;
    background: var(--card);
    box-shadow: 0 6px 18px rgba(0,0,0,0.18);
    overflow: hidden;
  }
  .card--front { left: 110px; top: 70px; }
  .card--back { left: 470px; top: 550px; }

  /* Front */
  .front-brand {
    position: absolute;
    left: 0; right: 0; top: 130px;
    display: flex; align-items: center; justify-content: center; gap: 18px;
  }
  .brand-dot {
    width: 86px; height: 86px; border-radius: 50%;
    background: var(--mark);
  }
  .brand-name {
    font-family: "Ubuntu", sans-serif;
    font-weight: 700;
    font-size: 60px;
    color: var(--ink);
    letter-spacing: -1px;
  }
  .front-web {
    position: absolute; left: 0; right: 0; bottom: 48px;
    text-align: center;
    font-family: "Michroma", sans-serif;
    font-size: 13px; letter-spacing: 3px;
    color: var(--ink-soft);
    text-transform: uppercase;
  }

  /* Back */
  .back-texture {
    position: absolute; left: 0; top: 0; width: 100%; height: 100%;
    background:
      linear-gradient(120deg, rgba(253,230,200,0.55) 0%, rgba(255,255,255,0) 38%),
      linear-gradient(300deg, rgba(253,230,200,0.45) 0%, rgba(255,255,255,0) 35%);
  }
  .back-swirls { position: absolute; inset: 0; }
  .back-mark {
    position: absolute; right: 52px; top: 42px;
    width: 112px; height: 112px; border-radius: 50%;
    background: var(--mark);
  }
  .person { position: absolute; left: 36px; top: 262px; }
  .person-name {
    font-weight: 700; font-size: 24px; color: var(--orange);
  }
  .person-role {
    margin-top: 6px;
    font-size: 10px; letter-spacing: 2.4px;
    color: var(--ink-soft);
  }
  .contact {
    position: absolute; left: 322px; top: 246px;
    width: 286px;
    list-style: none;
  }
  .contact li {
    display: flex; align-items: center; gap: 8px;
    height: 20px;
    font-family: "Michroma", sans-serif;
    font-size: 8px; letter-spacing: 0.5px;
    color: var(--ink);
    text-transform: uppercase;
    white-space: nowrap;
  }
  .contact li.contact-phone { font-size: 10px; letter-spacing: 1.5px; }
  .contact-icon {
    width: 15px; height: 15px; border-radius: 50%;
    background: var(--orange);
    display: flex; align-items: center; justify-content: center;
    flex: none;
  }
  .abn {
    position: absolute; right: 16px; bottom: 12px;
    font-size: 10px; color: var(--ink-soft);
  }
</style>
</head>
<body>

<section class="card card--front" aria-label="Card front">
  <div class="front-brand">
    <span class="brand-dot"></span>
    <span class="brand-name">RKT Advisory</span>
  </div>
  <p class="front-web">www.rktadvisory.example.com.au</p>
</section>

<section class="card card--back" aria-label="Card back">
  <div class="back-texture" role="img" aria-label="Faint pale orange checked texture"></div>
  <svg class="back-swirls" width="620" height="378" viewBox="0 0 620 378" aria-hidden="true">
    <path d="M0 150 C120 40 240 60 300 170 C360 280 470 300 620 330" fill="none" stroke="#fbd7a8" stroke-width="4"/>
    <path d="M130 0 C200 80 250 150 280 200 C320 270 370 330 400 378" fill="none" stroke="#fde3c2" stroke-width="3"/>
    <path d="M0 120 C160 230 320 150 470 170 C540 180 590 230 620 260" fill="none" stroke="#fde6c8" stroke-width="2"/>
  </svg>
  <span class="back-mark"></span>

  <div class="person">
    <p class="person-name">Dorian Valecki</p>
    <p class="person-role">Business Development Manager</p>
  </div>

  <ul class="contact">
    <li class="contact-phone">
      <span class="contact-icon">
        <svg width="7" height="10" viewBox="0 0 7 10"><rect x="0.5" y="0.5" width="6" height="9" rx="1" fill="none" stroke="#fff"/></svg>
      </span>
      +61 455 207 318
    </li>
    <li>
      <span class="contact-icon">
        <svg width="9" height="7" viewBox="0 0 9 7"><rect x="0.5" y="0.5" width="8" height="6" fill="none" stroke="#fff"/><path d="M0.5 0.5 L4.5 4 L8.5 0.5" fill="none" stroke="#fff"/></svg>
      </span>
      dorian@rktadvisory.example.com.au
    </li>
    <li>
      <span class="contact-icon">
        <svg width="9" height="9" viewBox="0 0 9 9"><circle cx="4.5" cy="4.5" r="4" fill="none" stroke="#fff"/><path d="M0.5 4.5 H8.5 M4.5 0.5 V8.5" stroke="#fff"/></svg>
      </span>
      www.rktadvisory.example.com.au
    </li>
  </ul>

  <p class="abn">ABN 62 118 409 735</p>
</section>

</body>
</html>
```